FlexBRAVO Web Design Project

We would like a website design to go with the new logo. They want something to model this site: http://www.pelanderfisk.example
Using the blue (#3366FF) and green (#33CC33). Like the bight colors in the top half of the home page. Must have a mini form on the interior pages.
Also like this site for inspiration:
http://www.quellbanmedia.example/
- Must fit the brief you had from before.
Must have a mini form
- Doesn't have to have to pop up navigation over the slider on the home page.

```html
<!DOCTYPE html>
<html lang="en">
<head>
<meta charset="utf-8">
<title>FlexBRAVO – Communicating</title>
<link rel="stylesheet" href="https://fonts.googleapis.com/css2?family=Electrolize&family=Montserrat:wght@400;500;600;700&family=Arimo:wght@400&display=swap">
<style>
  :root {
    --blue: #3366ff;
    --green: #33cc33;
    --green-dark: #1fae1f;
    --grey-text: #666666;
    --dark: #232323;
    --dark-2: #1b1b1b;
    --light-text: #f0f0f0;
    --field-border: #8a8a8a;
    --footer-bg: #f1f1f1;
    --footer-text: #333333;
  }
  * { box-sizing: border-box; margin: 0; padding: 0; }
  html, body { width: 1108px; height: 1200px; overflow: hidden; }
  body {
    position: relative;
    background: linear-gradient(170deg, #ffffff 0%, #f4f4f4 45%, #ffffff 100%);
    font-family: "Arimo", Arial, sans-serif;
  }
  .page { position: absolute; inset: 0; }

  .brand {
    position: absolute; left: 71px; top: 30px;
    display: flex; align-items: center; gap: 12px;
    font-family: "Montserrat", sans-serif; font-weight: 500;
    font-size: 66px; color: var(--grey-text); letter-spacing: -1px;
  }
  .brand-dot { width: 16px; height: 16px; border-radius: 50%; background: var(--blue); }

  .main-nav {
    position: absolute; left: 78px; top: 134px;
    display: flex; gap: 25px; list-style: none;
    font-family: "Montserrat", sans-serif; font-weight: 600;
    font-size: 16.5px; color: var(--blue); letter-spacing: 0.3px;
  }

  .hero-title {
    position: absolute; left: 70px; top: 168px;
    font-family: "Electrolize", sans-serif; font-size: 116px;
    color: var(--green); letter-spacing: -2px; line-height: 1.1;
  }
  .hero-sub {
    position: absolute; left: 75px; top: 274px;
    font-family: "Electrolize", sans-serif; font-size: 27px;
    color: var(--grey-text);
  }

  .stage-shapes { position: absolute; left: 0; top: 0; width: 1108px; height: 1200px; }

  .quote-tab {
    position: absolute; left: 696px; top: 307px; width: 352px; height: 46px;
    background: var(--blue); border-radius: 6px 6px 0 0;
    display: flex; align-items: center; gap: 10px; padding-left: 20px;
    font-family: "Montserrat", sans-serif; font-weight: 700; font-size: 17px; color: #fff;
  }

  .intro {
    position: absolute; left: 66px; top: 406px; width: 628px;
    color: var(--light-text); font-size: 15.4px; line-height: 18.8px; text-align: justify;
  }
  .intro p + p { margin-top: 18px; }

  .mini-form { position: absolute; left: 718px; top: 398px; width: 312px; }
  .field {
    height: 45px; margin-bottom: 11.5px;
    border: 3px solid var(--field-border); border-radius: 4px; background: #fff;
    display: flex; align-items: center; gap: 10px; padding-left: 10px;
    font-family: "Montserrat", sans-serif; font-size: 16px; color: #555;
    position: relative;
  }
  .field-select-arrow {
    position: absolute; right: 0; top: 0; bottom: 0; width: 38px;
    background: #3c3c3c; display: flex; align-items: center; justify-content: center;
  }
  .submit-quote {
    display: flex; align-items: center; justify-content: center;
    width: 313px; height: 41px; margin-top: 2px; border-radius: 3px;
    background: linear-gradient(#3fdc3f, var(--green-dark));
    font-family: "Montserrat", sans-serif; font-weight: 700; font-size: 16.5px; color: #fff;
    letter-spacing: 0.4px;
  }

  .feature { position: absolute; top: 726px; width: 307px; }
  .feature-photo { height: 160px; background: linear-gradient(135deg, #f2f2f2, #b5b5b5 60%, #707070); }
  .feature-title {
    height: 45px; background: rgba(51, 102, 255, 0.92);
    font-family: "Montserrat", sans-serif; font-size: 23px; font-weight: 500;
    color: #fff; padding: 8px 0 0 14px;
  }
  .feature-text { margin-top: 17px; color: var(--light-text); font-size: 16px; line-height: 20px; text-align: justify; }
  .read-more {
    position: absolute; top: 336px; left: 0;
    font-family: "Montserrat", sans-serif; font-weight: 700; font-size: 12.5px;
    color: var(--green); letter-spacing: 0.5px;
  }

  .site-footer {
    position: absolute; left: 0; top: 1121px; width: 1108px; height: 79px;
    background: linear-gradient(#e9e9e9, #ffffff 60%);
  }
  .copyright {
    position: absolute; left: 70px; top: 31px;
    font-family: "Montserrat", sans-serif; font-size: 12.5px; color: var(--footer-text);
    letter-spacing: 0.3px;
  }
  .copyright .terms { color: var(--blue); }
  .copyright .sep { margin: 0 7px; }
  .footer-brand {
    position: absolute; right: 78px; top: 17px;
    font-family: "Montserrat", sans-serif; font-weight: 500; font-size: 31px; color: var(--grey-text);
  }
</style>
</head>
<body>
<div class="page">
  <svg class="stage-shapes" viewBox="0 0 1108 1200" aria-hidden="true">
    <defs>
      <linearGradient id="darkFill" x1="0" y1="0" x2="0" y2="1">
        <stop offset="0" stop-color="#2c2c2c"/>
        <stop offset="1" stop-color="#1a1a1a"/>
      </linearGradient>
    </defs>
    <polygon points="0,387 1108,355 1108,1121 0,1121" fill="url(#darkFill)"/>
    <polygon points="0,357 1108,343 1108,356 0,388" fill="#3366ff"/>
  </svg>

  <div class="brand"><span>FlexBRAVO</span><span class="brand-dot"></span></div>

  <ul class="main-nav">
    <li>WHO WE ARE</li><li>WHAT WE DO</li><li>COMMUNITY</li><li>CAREERS</li><li>CONTACT</li>
  </ul>

  <h1 class="hero-title">Communicating</h1>
  <p class="hero-sub">Enterprise Technology clients.</p>

  <div class="quote-tab">
    <svg width="32" height="32" viewBox="0 0 32 32" aria-hidden="true">
      <circle cx="16" cy="16" r="14" fill="none" stroke="#fff" stroke-width="2.5"/>
      <path d="M11 21 l1.5-5 7-7 3.5 3.5-7 7z" fill="#fff"/>
    </svg>
    <span>FREE QUOTE</span>
  </div>

  <div class="intro">
    <p>Lorem ipsum dolor sit amet, consectetur adipiscing elit. Nunc eu massa sem, venenatis adipiscing nulla. Sed tempor posuere orci sit amet gravida. Aenean nisi augue, bibendum in ornare eget, volutpat porta sapien. Suspendisse viverra sagittis arcu, euismod luctus dui euismod sed. Aenean tincidunt, justo blandit interdum tincidunt, erat odio sagittis orci, pulvinar ullamcorper neque diam volutpat augue. Suspendisse at lobortis felis. Nunc aliquam risus quis augue gravida porta. Maecenas erat tellus, pretium consectetur semper ut, placerat nec velit.</p>
    <p>Morbi vel nibh ut leo ullamcorper hendrerit sed id augue. Aenean non leo justo. Cum sociis natoque penatibus et magnis dis parturient montes, nascetur ridiculus mus. Maecenas erat tellus, pretium consectetur semper ut, placerat nec velit. Morbi luctus fermentum libero eu gravida. Quisque sodales erat non urna sodales convallis sit amet vitae leo. Ut et elit ac arcu convallis vestibulum non non ligulln ultrices lacus.</p>
  </div>

  <form class="mini-form">
    <div class="field">
      <svg width="20" height="20" viewBox="0 0 20 20" aria-hidden="true"><circle cx="10" cy="6" r="4.5" fill="#999"/><path d="M2 19c0-5 3.5-7.5 8-7.5s8 2.5 8 7.5z" fill="#999"/></svg>
      <span>name</span>
    </div>
    <div class="field">
      <svg width="20" height="20" viewBox="0 0 20 20" aria-hidden="true"><path d="M4 2l3 0 1.5 4-2 1.5c1 2.5 3 4.5 5.5 5.5l1.5-2 4 1.5 0 3c0 1-1 2-2 2C9 17.5 2.5 11 2.5 4c0-1 .5-2 1.5-2z" fill="#999"/></svg>
      <span>telephone</span>
    </div>
    <div class="field">
      <svg width="20" height="20" viewBox="0 0 20 20" aria-hidden="true"><rect x="2" y="5" width="16" height="11" fill="#999"/><path d="M2 5l8 6 8-6" fill="none" stroke="#fff" stroke-width="1.4"/></svg>
      <span>email</span>
    </div>
    <div class="field">
      <svg width="20" height="20" viewBox="0 0 20 20" aria-hidden="true"><path d="M11 2l7 7-2 1-3 3 0 3-1 1-3.5-3.5L3 18l-1 0 0-1 4.5-5.5L3 8l1-1 3 0 3-3z" fill="#999"/></svg>
      <span>interested in</span>
      <span class="field-select-arrow">
        <svg width="12" height="18" viewBox="0 0 12 18" aria-hidden="true"><path d="M6 2l4 5H2zM6 16l4-5H2z" fill="#ddd"/></svg>
      </span>
    </div>
    <div class="submit-quote">GET A FREE QUOTE</div>
  </form>

  <article class="feature" style="left:72px">
    <div class="feature-photo" role="img" aria-label="Black and white photo of colleagues working at a desk with papers and a laptop"></div>
    <h2 class="feature-title">Heading One</h2>
    <p class="feature-text">Lorem ipsium dolor sit amet, consect etur adipiscloing elit. Nunc eu massa sem, venenatis adipiscing nulla. Sed tempor posulore iere orci sit amet gra vida. Aenean nisi augue, biben dum.</p>
    <span class="read-more">+ READ MORE</span>
  </article>

  <article class="feature" style="left:400px">
    <div class="feature-photo" role="img" aria-label="Black and white photo of a smiling young man giving a thumbs up"></div>
    <h2 class="feature-title">Heading Two</h2>
    <p class="feature-text">Lorem ipsium dolor sit amet, consect etur adipiscloing elit. Nunc eu massa sem, venenatis adipiscing nulla. Sed tempor posulore iere orci sit amet gra vida. Aenean nisdum in ornare eget.</p>
    <span class="read-more">+ READ MORE</span>
  </article>

  <article class="feature" style="left:729px;width:302px">
    <div class="feature-photo" role="img" aria-label="Black and white photo of three business people meeting around a laptop"></div>
    <h2 class="feature-title">Heading Three</h2>
    <p class="feature-text">Lorem ipsium dolor sit amet, consect etur adipiscloing elit. Nunc eu massa sem, venenatis adipiscing nulla. Sed tempor posulore ieregue, biben dum in ornare eget.</p>
    <span class="read-more">+ READ MORE</span>
  </article>

  <footer class="site-footer">
    <p class="copyright">COPYRIGHT © 2012 FLEXBRAVO. ALL RIGHTS RESERVED.<span class="sep">|</span><span class="terms">TERMS OF USE</span></p>
    <div class="footer-brand">FlexBRAVO</div>
  </footer>
</div>
</body>
</html>
```